specialised legal consultancy business needs an update on logo and office stationary.

Update on Logo - see attached.

update on email signature - something new and fresh with only the following details -

(the logo)
Advocate Pieter Vosloo
PV Entity Frameworks (Pty) Ltd (Reg No.: 2019 / 352917 / 07)
LLB, LLM (Cum Laude), Cert.Dir (BFNTA), FCG (PRWEK)
+27 61 552 9047
pieter#vosloolegal.com

Update on letterhead - something new and fresh and please more user-friendly. With the same details as per the email signature.

```html
<!DOCTYPE html>
<html lang="en">
<head>
<meta charset="utf-8">
<title>Email Signature – PV Frameworks</title>
<link rel="stylesheet" href="https://fonts.googleapis.com/css2?family=Poppins:wght@300;400;500;600;700&display=swap">
<style>
  :root {
    --bg-top: #f4f3f1;
    --bg-bottom: #e9e8e6;
    --ink: #000000;
    --text: #2a2a2a;
    --card: #ffffff;
    --note: #ff1a1a;
  }
  * { margin: 0; padding: 0; box-sizing: border-box; }
  html, body { width: 1200px; height: 1200px; overflow: hidden; }
  body {
    position: relative;
    font-family: "Poppins", sans-serif;
    background: linear-gradient(180deg, var(--bg-top), var(--bg-bottom));
    color: var(--text);
  }
  .board-title {
    position: absolute; top: 74px; left: 0; width: 100%;
    text-align: center; font-size: 26px; font-weight: 600; color: #111;
  }
  .board-note {
    position: absolute; top: 110px; left: 0; width: 100%;
    text-align: center; font-size: 19px; font-weight: 300; color: var(--note);
  }
  .signature {
    position: absolute; left: 234px; top: 225px; width: 732px; height: 751px;
    background: var(--card);
    box-shadow: 0 6px 24px rgba(0,0,0,0.14);
  }
  .rail-thick { position: absolute; left: 0; top: 0; width: 20px; height: 100%; background: var(--ink); }
  .rail-thin { position: absolute; left: 26px; top: 0; width: 6px; height: 100%; background: var(--ink); }
  .brand-mark {
    position: absolute; left: 138px; top: 70px; width: 170px; height: 170px; background: var(--ink);
  }
  .brand-name {
    position: absolute; left: 60px; top: 300px;
    font-size: 35px; font-weight: 700; letter-spacing: 5px; color: var(--ink);
  }
  .role { position: absolute; left: 60px; top: 404px; font-size: 30px; font-weight: 400; color: var(--ink); letter-spacing: 1px; }
  .name { position: absolute; left: 60px; top: 438px; font-size: 35px; font-weight: 700; color: var(--ink); letter-spacing: 0.5px; }
  .rule { position: absolute; left: 60px; width: 646px; height: 2px; background: var(--ink); }
  .rule-top { top: 499px; }
  .rule-bottom { top: 621px; }
  .detail { position: absolute; left: 60px; font-size: 17px; font-weight: 500; letter-spacing: 0.6px; }
  .detail-company { top: 533px; }
  .detail-quals { top: 573px; }
  .contact { position: absolute; left: 60px; display: flex; align-items: center; font-size: 18px; font-weight: 500; letter-spacing: 0.6px; }
  .contact svg { width: 18px; height: 18px; margin-right: 14px; fill: var(--ink); }
  .contact-phone { top: 656px; }
  .contact-email { top: 686px; }
</style>
</head>
<body>
  <h1 class="board-title">email signature Mockup 2</h1>
  <p class="board-note">***Size: 600px width- RESPONSIVE -  Viewable in all media</p>

  <section class="signature">
    <div class="rail-thick"></div>
    <div class="rail-thin"></div>

    <div class="brand-mark"></div>
    <div class="brand-name">PV FRAMEWORKS</div>

    <div class="role">Advocate</div>
    <div class="name">Pieter Vosloo</div>

    <div class="rule rule-top"></div>
    <p class="detail detail-company">PV Entity Frameworks (Pty) Ltd (Reg No.: 2019 / 352917 / 07)</p>
    <p class="detail detail-quals">LLB, LLM (Cum Laude), Cert.Dir (BFNTA), FCG (PRWEK)</p>
    <div class="rule rule-bottom"></div>

    <div class="contact contact-phone">
      <svg viewBox="0 0 24 24" aria-hidden="true"><path d="M6.6 10.8a15.1 15.1 0 0 0 6.6 6.6l2.2-2.2c.3-.3.7-.4 1-.2 1.1.4 2.3.6 3.6.6.6 0 1 .4 1 1V20c0 .6-.4 1-1 1C10.6 21 3 13.4 3 4c0-.6.4-1 1-1h3.5c.6 0 1 .4 1 1 0 1.3.2 2.5.6 3.6.1.3 0 .7-.2 1L6.6 10.8z"/></svg>
      +27 61 552 9047
    </div>
    <div class="contact contact-email">
      <svg viewBox="0 0 24 24" aria-hidden="true"><path d="M2 5h20v2.2l-10 6.3L2 7.2z"/><path d="M2 9.6l10 6.3 10-6.3V19H2z"/></svg>
      pieter#vosloolegal.com
    </div>
  </section>
</body>
</html>
```